Harbor Crest Holdings Corporate Showcase

Provide an attractive Corporate Website for a boutique Investment Company to showcase our activities and corporate interests.

Our Company works across a number of Sectors including

Real Estate
E-Commerce
Healthcare
Beauty & Personal Care
Technology
Resources

Lets keep the personality

Modern
Global
Sophisticated
Calm
Interesting

Lets keep the pages with MINIMAL Words
Lets use Photos/ Imagery to tell the story

We'll need a Banner Menu -
About Us
Expertise
Global Outlook
Sectors
Management
Media
Contact Us

Many thanks
Best wishes
Dennis.

Target Market(s)

Investors
Clients

Coding

Coded - Design and coding required

Number of Pages Required

5+ page

Font styles to use
Sans Serif

Colors
886aae
3176b5
00a990
f68e4d
f04a50
e667a6

Requirements
Must have
• WordPress Coding

Checkout this Website for look and feel - its cool:
www.qvr-example.com

Harbor Crest Partners
(Harbor Crest Holdings LLP)
London
E9 4ZX
United Kingdom

www.HarborCrestPartners-example.com
Nice to have
• Sophisticated colour palette - black/ brown/ blue/ purple/

```html
<!DOCTYPE html>
<html lang="en">
<head>
<meta charset="utf-8">
<title>Harbor Crest Holdings</title>
<link href="https://fonts.googleapis.com/css2?family=Montserrat:wght@400;500;600;700;800&display=swap" rel="stylesheet">
<style>
:root{
  --purple:#886aae;--blue:#3176b5;--green:#00a990;--orange:#f68e4d;--red:#f04a50;--pink:#e667a6;
  --navy:#0b1630;--ink:#222;--text:#6a6a6a;--rule:#e4e4e4;--teal:#13a382;--footer:#2b5aa3;--white:#fff;
}
*{margin:0;padding:0;box-sizing:border-box}
html,body{width:1200px;height:3716px;overflow:hidden}
body{font-family:'Montserrat',sans-serif;color:var(--ink);background:var(--white);position:relative}
.abs{position:absolute}

/* hero */
.hero{left:0;top:0;width:1200px;height:640px;background:radial-gradient(ellipse at 70% 60%,#1d3a7a 0%,#0f2150 35%,var(--navy) 75%)}
.hero-city{left:0;top:0;width:1200px;height:640px;background:linear-gradient(180deg,rgba(10,20,45,.2),rgba(40,70,140,.35) 60%,rgba(10,20,45,.6))}
.brand{left:0;top:30px;width:1200px;text-align:center;color:var(--white);font-weight:700;font-size:34px;letter-spacing:1px}
.nav{left:0;top:108px;width:1200px;display:flex;justify-content:center;gap:40px}
.nav a{color:var(--white);text-decoration:none;font-size:14px;font-weight:600;letter-spacing:.5px;padding-bottom:8px}
.nav a.active{border-bottom:2px solid var(--white)}
.hero-title{left:0;top:250px;width:1200px;text-align:center;color:var(--white);line-height:1.05}
.hero-title .l1{font-size:74px;font-weight:400;letter-spacing:2px;display:block}
.hero-title .l2{font-size:74px;font-weight:800;letter-spacing:2px;display:block}
.watch{left:530px;top:446px;width:140px;height:44px;border:2px solid var(--white);border-radius:22px;color:var(--white);font-size:13px;font-weight:700;display:flex;align-items:center;justify-content:center;gap:8px}
.notch{left:570px;top:612px;width:60px;height:60px;background:var(--white);transform:rotate(45deg);border-radius:6px}

/* sectors */
.section-title{left:0;width:1200px;text-align:center;font-size:44px;font-weight:400;letter-spacing:2px;color:#333}
.section-title b{font-weight:800;color:var(--ink)}
.sector-grid{left:140px;top:840px;width:920px;height:760px;display:grid;grid-template-columns:repeat(3,1fr);grid-template-rows:repeat(2,1fr)}
.sector{text-align:center;padding:34px 30px 0}
.sector:nth-child(-n+3){border-bottom:1px solid var(--rule)}
.sector:nth-child(3n+1),.sector:nth-child(3n+2){border-right:1px solid var(--rule)}
.sector svg{width:74px;height:74px}
.sector h3{font-size:17px;font-weight:600;margin:26px 0 14px;letter-spacing:.5px}
.sector p{font-size:12.5px;line-height:1.6;color:var(--text)}
.more{display:inline-flex;align-items:center;gap:6px;margin-top:32px;height:36px;padding:0 24px;border:2px solid;border-radius:18px;font-size:11px;font-weight:700;color:#333}

/* about */
.about-panel{left:88px;top:1760px;width:1112px;height:528px;background:var(--teal)}
.about-photo{left:0;top:1672px;width:490px;height:510px;background:linear-gradient(135deg,#5f6a78,#2a3140 50%,#b5b2aa);border:10px solid var(--white)}
.about-body{left:560px;top:1806px;width:590px;color:var(--white)}
.about-body h2{font-size:46px;font-weight:400;line-height:1.1;letter-spacing:1px}
.about-body h2 b{font-weight:800;display:block}
.about-body hr{width:110px;border:0;border-top:2px solid var(--white);margin:24px 0}
.about-body p{font-size:13px;line-height:1.75;margin-bottom:10px}

/* blog */
.post-img{background:linear-gradient(135deg,#d9b28a,#ece6dc 45%,#7f8b9d)}
.post-img.alt{background:linear-gradient(135deg,#e9eef4,#a9b7c9 50%,#4e5f78)}
.post-text{width:420px}
.meta{font-size:12px;color:#555;display:flex;align-items:center;gap:8px}
.meta i{width:10px;height:10px;background:var(--blue);display:inline-block}
.post-text h3{font-size:18px;font-weight:700;line-height:1.4;margin:26px 0 16px}
.post-text p{font-size:12.5px;line-height:1.7;color:var(--text)}
.post-text .more{border-color:var(--orange)}

/* footer */
.footer{left:0;top:3352px;width:1200px;height:364px;background:var(--footer);color:var(--white)}
.fnotch{left:570px;top:3322px;width:60px;height:60px;background:var(--footer);transform:rotate(45deg);border-radius:6px}
.fcol h4{font-size:17px;font-weight:700;letter-spacing:.5px;margin-bottom:26px}
.flinks{display:grid;grid-template-columns:150px 150px;row-gap:12px;font-size:13px}
.social{display:flex;gap:20px;margin-bottom:24px}
.social span{width:28px;height:28px;border-radius:50%;background:var(--white);display:block}
.copy{font-size:12px}
</style>
</head>
<body>

<header>
  <div class="abs hero" role="img" aria-label="Night city skyline with financial chart lines"></div>
  <div class="abs hero-city"></div>
  <svg class="abs" style="left:400px;top:380px" width="800" height="200" viewBox="0 0 800 200"><polyline points="0,180 120,150 200,170 300,110 380,130 470,70 560,90 650,30 800,10" fill="none" stroke="#f04a50" stroke-width="2" opacity=".8"/></svg>
  <div class="abs brand">HARBOR CREST HOLDINGS</div>
  <nav class="abs nav">
    <a class="active">HOME</a><a>ABOUT US</a><a>EXPERTISE</a><a>GLOBAL OUTLOOK</a><a>SECTORS</a><a>MANAGEMENT</a><a>MEDIA</a><a>CONTACT US</a>
  </nav>
  <h1 class="abs hero-title"><span class="l1">HARBOR CREST</span><span class="l2">INVESTMENTS</span></h1>
  <div class="abs watch">WATCH VIDEO <svg width="16" height="16" viewBox="0 0 16 16"><circle cx="8" cy="8" r="7.5" fill="#fff"/><path d="M6 4.5v7l5.5-3.5z" fill="#0b1630"/></svg></div>
  <div class="abs notch"></div>
</header>

<section>
  <h2 class="abs section-title" style="top:714px">OUR <b>SECTORS</b></h2>
  <div class="abs sector-grid">
    <div class="sector">
      <svg viewBox="0 0 74 74" fill="none" stroke="var(--purple)" stroke-width="2.5"><path d="M8 36 37 12l29 24"/><path d="M16 30v32h42V30"/><rect x="30" y="42" width="14" height="20"/><rect x="20" y="36" width="8" height="8"/><rect x="46" y="36" width="8" height="8"/></svg>
      <h3>REAL ESTATE</h3>
      <p>Lorem ipsum dolor sit amet consectetur adipiscing elit sed do eiusmod tempor incididunt ut labore et dolore magna aliqua</p>
      <div class="more" style="border-color:var(--purple)">READ MORE <span style="color:var(--purple)">➜</span></div>
    </div>
    <div class="sector">
      <svg viewBox="0 0 74 74" fill="none" stroke="var(--blue)" stroke-width="2.5"><rect x="8" y="12" width="58" height="44" rx="3"/><path d="M8 22h58"/><path d="M20 32h6l5 14h16l4-10H29"/><circle cx="33" cy="50" r="2"/><circle cx="45" cy="50" r="2"/><path d="M28 62h18"/></svg>
      <h3>E-COMMERCE</h3>
      <p>Lorem ipsum dolor sit amet consectetur adipiscing elit sed do eiusmod tempor incididunt ut labore et dolore magna aliqua</p>
      <div class="more" style="border-color:var(--blue)">READ MORE <span style="color:var(--blue)">➜</span></div>
    </div>
    <div class="sector">
      <svg viewBox="0 0 74 74" fill="none" stroke="var(--green)" stroke-width="2.5"><path d="M37 64S8 46 8 26a14 14 0 0 1 29-6 14 14 0 0 1 29 6c0 20-29 38-29 38z"/><path d="M37 28v18M28 37h18"/></svg>
      <h3>HEALTHCARE</h3>
      <p>Lorem ipsum dolor sit amet consectetur adipiscing elit sed do eiusmod tempor incididunt ut labore et dolore magna aliqua</p>
      <div class="more" style="border-color:var(--green)">READ MORE <span style="color:var(--green)">➜</span></div>
    </div>
    <div class="sector">
      <svg viewBox="0 0 74 74" fill="none" stroke="var(--orange)" stroke-width="2.5"><circle cx="37" cy="37" r="26"/><path d="M37 20c8 10 8 24 0 34-8-10-8-24 0-34z"/><path d="M20 37h34"/></svg>
      <h3>BEAUTY &amp; PERSONAL CARE</h3>
      <p>Lorem ipsum dolor sit amet consectetur adipiscing elit sed do eiusmod tempor incididunt ut labore et dolore magna aliqua</p>
      <div class="more" style="border-color:var(--orange)">READ MORE <span style="color:var(--orange)">➜</span></div>
    </div>
    <div class="sector">
      <svg viewBox="0 0 74 74" fill="none" stroke="var(--red)" stroke-width="2.5"><rect x="18" y="18" width="38" height="38" rx="3"/><rect x="28" y="28" width="18" height="18"/><path d="M26 8v10M37 8v10M48 8v10M26 56v10M37 56v10M48 56v10M8 26h10M8 37h10M8 48h10M56 26h10M56 37h10M56 48h10"/></svg>
      <h3>TECHNOLOGY</h3>
      <p>Lorem ipsum dolor sit amet consectetur adipiscing elit sed do eiusmod tempor incididunt ut labore et dolore magna aliqua</p>
      <div class="more" style="border-color:var(--red)">READ MORE <span style="color:var(--red)">➜</span></div>
    </div>
    <div class="sector">
      <svg viewBox="0 0 74 74" fill="none" stroke="var(--pink)" stroke-width="2.5"><circle cx="37" cy="37" r="10"/><circle cx="37" cy="37" r="18" stroke-dasharray="6 5"/><circle cx="14" cy="14" r="6"/><circle cx="60" cy="14" r="6"/><circle cx="14" cy="60" r="6"/><circle cx="60" cy="60" r="6"/></svg>
      <h3>RESOURCES</h3>
      <p>Lorem ipsum dolor sit amet consectetur adipiscing elit sed do eiusmod tempor incididunt ut labore et dolore magna aliqua</p>
      <div class="more" style="border-color:var(--pink)">READ MORE <span style="color:var(--pink)">➜</span></div>
    </div>
  </div>
</section>

<section>
  <div class="abs about-panel"></div>
  <div class="abs about-photo" role="img" aria-label="Business meeting with documents and charts on a desk"></div>
  <div class="abs about-body">
    <h2>ABOUT<b>HARBOR CREST INVESTMENTS</b></h2>
    <hr>
    <p>Lorem ipsum dolor sit amet, consectetur adipiscing elit sed do eiusmod tempor incididunt ut labore et dolore magna aliqua. Ut enim ad minim veniam quis nostrud exercitation ullamco laboris nisi ut aliquip ex ea commodo consequat.</p>
    <p>Duis aute irure dolor in reprehenderit in voluptate velit esse cillum dolore eu fugiat nulla pariatur. Excepteur sint occaecat cupidatat non proident sunt in culpa qui officia deserunt mollit anim id est laborum.</p>
  </div>
</section>

<section>
  <h2 class="abs section-title" style="top:2424px">BLOG <b>POSTS</b></h2>
  <div class="abs post-img" style="left:260px;top:2512px;width:320px;height:376px" role="img" aria-label="Hands reviewing financial documents on a desk"></div>
  <article class="abs post-text" style="left:588px;top:2540px">
    <div class="meta"><i></i>Dec 10,2020 / Comments</div>
    <h3>LOREM IPSUM DOLOR SIT AMETON<br>ECTETUR ADIPISCING</h3>
    <p>Lorem ipsum dolor sit amet consectetur adipiscing elit sed do eiusmod tempor incididunt ut labore et dolore magna aliqua. Ut enim ad minim veniam quis nostrud exercitation ullamco laboris nisi ut aliquip ex ea commodo consequat. Duis aute irure dolor in reprehenderit.</p>
    <div class="more">READ MORE <span style="color:var(--orange)">➜</span></div>
  </article>
  <article class="abs post-text" style="left:150px;top:3012px">
    <div class="meta"><i></i>Dec 10,2020 / Comments</div>
    <h3>LOREM IPSUM DOLOR SIT AMETON<br>ECTETUR ADIPISCING</h3>
    <p>Lorem ipsum dolor sit amet consectetur adipiscing elit sed do eiusmod tempor incididunt ut labore et dolore magna aliqua. Ut enim ad minim veniam quis nostrud exercitation ullamco laboris nisi ut aliquip ex ea commodo consequat. Duis aute irure dolor in reprehenderit.</p>
    <div class="more">READ MORE <span style="color:var(--orange)">➜</span></div>
  </article>
  <div class="abs post-img alt" style="left:680px;top:2980px;width:370px;height:280px" role="img" aria-label="Analyst at a desk with laptop and charts"></div>
</section>

<footer>
  <div class="abs footer"></div>
  <div class="abs fnotch"></div>
  <div class="abs fcol" style="left:140px;top:3430px">
    <h4>QUICK LINKS</h4>
    <div class="flinks" style="grid-template-columns:120px 120px"><span>Home</span><span>Management</span><span>About Us</span><span>Media</span><span>Expertise</span><span>Contact Us</span><span>Global Outlook</span></div>
  </div>
  <div class="abs fcol" style="left:448px;top:3430px">
    <h4>OUR SECTORS</h4>
    <div class="flinks"><span>Real Estate</span><span>Technology</span><span>E-Commerce</span><span>Resources</span><span>Healthcare</span><span></span><span>Beauty &amp; Personal Care</span></div>
  </div>
  <div class="abs fcol" style="left:760px;top:3430px">
    <h4>STAY CONNECTED</h4>
    <div class="social"><span></span><span></span><span></span><span></span></div>
    <div class="copy">2020 Harbor Crest Holdings All rights reserved</div>
  </div>
</footer>

</body>
</html>
```